Contemporary new French wine brand needs logo and series of label design

to design a new contemporary logo and series of labels for a new French wine brand. We hope to attract not just current French wine drinkers but new ones who may appreciate a less traditional and more modern style.
Updates

Reason: we are wanting to extend the project for a few days more to receive more submissions since we had fewer designs submitted than we were expecting, maybe because of the holidays.

Target Market(s)

people who follow the arts community (eg. music, theatre, visual/video arts, dance) --- all mature ages.

Industry/Entity Type

French Wine

Requirements
Must have
• a clear, memorable treatment for the name MORIVAL with accompanying logo.
Nice to have
• embossing, matte/gloss refinement, tasteful foil stamping, coated stock for the whites to help the integrity of the paper in and out of ice buckets. A combo of say, three types of fonts; a semi custom font for the brand name Morival and maybe a script and one other.
Should not have
• not traditional French

```html
<!DOCTYPE html>
<html lang="en">
<head>
<meta charset="utf-8">
<title>Morival — Muscadet label</title>
<link rel="stylesheet" href="https://fonts.googleapis.com/css2?family=Source+Sans+3:wght@400&family=Dancing+Script:wght@500&family=Crimson+Text&display=swap">
<style>
  :root {
    --glass: #5f9e2a;
    --glass-light: #7cb636;
    --silver-dark: #b9b9b9;
    --silver-light: #ececec;
    --frame: #d6d6d6;
    --brand-grey: #9a9a9a;
    --varietal-green: #6fae2c;
    --region-ink: #2f3a24;
  }
  html, body {
    margin: 0;
    padding: 0;
    overflow: hidden;
  }
  .canvas {
    position: relative;
    width: 753px;
    height: 1200px;
    background: linear-gradient(90deg, var(--glass) 0%, var(--glass-light) 55%, var(--glass) 100%);
    overflow: hidden;
  }
  .foil-band {
    position: absolute;
    left: 66px;
    top: 607px;
    width: 620px;
    height: 285px;
    background: linear-gradient(90deg, var(--silver-dark) 0%, var(--silver-light) 100%);
  }
  .label-frame {
    position: absolute;
    left: 88px;
    top: 330px;
    width: 575px;
    height: 540px;
    border: 3px solid var(--frame);
    box-sizing: border-box;
  }
  .brand-mark {
    position: absolute;
    left: 362px;
    top: 402px;
    width: 28px;
    height: 28px;
    border: 3px solid var(--brand-grey);
    box-sizing: border-box;
  }
  .brand-name {
    position: absolute;
    left: 0;
    width: 753px;
    top: 522px;
    margin: 0;
    text-align: center;
    font-family: "Source Sans 3", sans-serif;
    font-weight: 400;
    font-size: 74px;
    line-height: 1;
    color: var(--brand-grey);
  }
  .varietal {
    position: absolute;
    left: 0;
    width: 753px;
    top: 722px;
    margin: 0;
    text-align: center;
    font-family: "Dancing Script", cursive;
    font-weight: 500;
    font-size: 30px;
    letter-spacing: 9px;
    color: var(--varietal-green);
  }
  .region {
    position: absolute;
    left: 0;
    width: 753px;
    top: 836px;
    margin: 0;
    text-align: center;
    font-family: "Crimson Text", serif;
    font-size: 24px;
    color: var(--region-ink);
  }
</style>
</head>
<body>
  <main class="canvas">
    <div class="foil-band"></div>
    <div class="label-frame"></div>
    <div class="brand-mark"></div>
    <h1 class="brand-name">Morival</h1>
    <p class="varietal">Muscadet</p>
    <p class="region">burgundy</p>
  </main>
</body>
</html>
```